Brivolt Technologies business card design

We need a business card designed with our new logo. it would be great if the card could communicate it is a technology based company.

Target Market(s)

system integrators

Industry/Entity Type

technology, IOT

Contact Information for Business Card

Name, designation, Address, telephone number, email address

Requirements
Must have
• logo and company name
Nice to have
• something to do with technology

```html
<!DOCTYPE html>
<html lang="en">
<head>
<meta charset="utf-8">
<title>Brivolt Technologies Business Card</title>
<link href="https://fonts.googleapis.com/css2?family=Arimo:wght@400;700&display=swap" rel="stylesheet">
<style>
  :root {
    --stage: #161616;
    --card: #2f2f31;
    --orange: #f7941d;
    --white: #ffffff;
    --soft: #e6e6e6;
  }
  * { margin: 0; padding: 0; box-sizing: border-box; }
  html, body { width: 1200px; height: 900px; overflow: hidden; }
  body {
    background: var(--stage);
    font-family: "Arimo", Arial, sans-serif;
    display: flex;
    flex-direction: column;
    align-items: center;
    justify-content: center;
    gap: 54px;
  }
  .card {
    position: relative;
    width: 600px;
    height: 343px;
    background: var(--card);
    border-radius: 18px;
    overflow: hidden;
    box-shadow: 0 10px 28px rgba(0,0,0,.55);
  }

  /* Front */
  .front-brand {
    position: absolute;
    top: 46px;
    left: 0;
    right: 0;
    text-align: center;
    display: flex;
    justify-content: center;
    align-items: center;
    gap: 10px;
  }
  .brand-mark {
    width: 14px;
    height: 14px;
    background: var(--orange);
  }
  .brand-name {
    font-weight: 700;
    font-size: 26px;
    letter-spacing: 2px;
    color: var(--white);
    text-transform: uppercase;
  }
  .contact {
    position: absolute;
    left: 44px;
    top: 138px;
    color: var(--soft);
    font-size: 14px;
    line-height: 1.45;
  }
  .address { margin-bottom: 14px; }
  .contact-line { display: flex; align-items: center; gap: 8px; }
  .contact-line svg { width: 13px; height: 13px; flex: none; }
  .person {
    position: absolute;
    right: 58px;
    top: 214px;
    text-align: right;
  }
  .person-name {
    color: var(--orange);
    font-weight: 700;
    font-size: 22px;
    text-transform: uppercase;
    letter-spacing: .5px;
  }
  .person-title {
    color: var(--soft);
    font-size: 14px;
    margin-top: 4px;
  }
  .edge-bar {
    position: absolute;
    right: 0;
    top: 216px;
    width: 26px;
    height: 46px;
    background: var(--orange);
  }

  /* Back */
  .back .back-brand {
    position: absolute;
    inset: 0;
    display: flex;
    justify-content: center;
    align-items: center;
    gap: 14px;
  }
  .back .brand-mark { width: 20px; height: 20px; }
  .back .brand-name { font-size: 36px; color: var(--orange); letter-spacing: 3px; }
</style>
</head>
<body>

  <section class="card front" aria-label="Card front">
    <div class="front-brand">
      <span class="brand-mark"></span>
      <span class="brand-name">Brivolt Technologies</span>
    </div>

    <div class="contact">
      <p class="address">1180 Harbor Lane<br>Westfield AB 4021</p>
      <p class="contact-line">
        <svg viewBox="0 0 16 16" aria-hidden="true"><path fill="#f7941d" d="M3.5 1.5l2.5 3-1.5 1.8c.9 2 2.3 3.4 4.2 4.2l1.8-1.5 3 2.5-1.6 2.5C6.8 13.6 2.4 9.2 1 3.1z"/></svg>
        (123) 481-3907
      </p>
      <p class="contact-line">
        <svg viewBox="0 0 16 16" aria-hidden="true"><rect x="1" y="3" width="14" height="10" fill="#f7941d"/><path d="M1 3l7 6 7-6" fill="none" stroke="#2f2f31" stroke-width="1.4"/></svg>
        info@brivolttech.com
      </p>
      <p class="contact-line">
        <svg viewBox="0 0 16 16" aria-hidden="true"><circle cx="8" cy="8" r="6.5" fill="none" stroke="#f7941d" stroke-width="1.5"/><path d="M1.5 8h13M8 1.5c-3 3.5-3 9.5 0 13M8 1.5c3 3.5 3 9.5 0 13" fill="none" stroke="#f7941d" stroke-width="1.2"/></svg>
        www.brivolttech.com
      </p>
    </div>

    <div class="person">
      <p class="person-name">Daniel Reuter</p>
      <p class="person-title">CEO/Founder</p>
    </div>
    <span class="edge-bar"></span>
  </section>

  <section class="card back" aria-label="Card back">
    <div class="back-brand">
      <span class="brand-mark"></span>
      <span class="brand-name">Brivolt Technologies</span>
    </div>
  </section>

</body>
</html>
```